Recruiting ad for Caregivers and Nurses

We need a few amazing, fun, catchy, creative recruiting ads for Caregivers and Nurses to care for homecare patients on the island of Oahu, in Hawaii. We are an in home care company called Palmer Homecare. Our care services are provided 24/7, so we need staff that can work days, nights, weekdays, weekends. We need catchy fun ads to entice caregivers and nurses to call our office to inquire about jobs available. Our patients age range is from babies to seniors. We need caregivers and nurses for basic patient care (bathing, dressing, ambulating, preparing meals, medication reminders, light housekeeping) and complex patients (oxygen, tube feeding, injections, vents, wound care). Here are some bullets to consider including:
*Full-time and Part-time Positions Available (days, nights, weekdays, weekends)
*Sign-On Bonus Programs Offered up to $500
*Refer a Friend Bonus Program
*Holiday Pay
*2 Health Plans to Choose from
*Island-Wide Locations
*All PPE Provided (masks, gloves, etc)
*401K Program
*Tuition Benefits

```html
<!DOCTYPE html>
<html lang="en">
<head>
<meta charset="utf-8">
<title>Palmer Homecare – Caregivers Wanted</title>
<link href="https://fonts.googleapis.com/css2?family=Kurale&family=Mulish:wght@400&display=swap" rel="stylesheet">
<style>
  :root {
    --teal: #006f62;
    --salmon: #f49a8a;
    --salmon-soft: #fbd8d0;
    --white: #ffffff;
  }
  * { margin: 0; padding: 0; box-sizing: border-box; }
  html, body { width: 1200px; height: 719px; overflow: hidden; background: var(--white); }
  .ad { position: relative; width: 1200px; height: 719px; background: var(--white); font-family: "Kurale", Georgia, serif; }
  .frame { position: absolute; left: 29px; top: 30px; width: 1141px; height: 645px; background: var(--teal); border-radius: 8px; }
  .panel-top { position: absolute; left: 42px; top: 43px; width: 1115px; height: 415px; background: var(--white); }
  .panel-contact { position: absolute; left: 42px; top: 611px; width: 1115px; height: 51px; background: var(--white); }

  .photo { position: absolute; top: 89px; width: 228px; height: 171px; border-radius: 29px; }
  .photo-team { left: 73px; background: linear-gradient(160deg, #7fa6c9 0%, #5d7d4a 35%, #8b2f3c 65%, #2c3e66 100%); }
  .photo-nurse { left: 342px; background: linear-gradient(120deg, #b9b7b1 0%, #8d8a84 45%, #2b2a2a 80%, #6b4a3a 100%); }
  .photo-board { left: 613px; background: radial-gradient(circle at 50% 45%, #3b3d45 0%, #24262d 70%, #1c1d22 100%); }

  .flourish { position: absolute; top: 262px; width: 228px; height: 76px; background: linear-gradient(180deg, var(--salmon-soft), rgba(251,216,208,0)); border-radius: 10px; }
  .flourish-1 { left: 73px; }
  .flourish-2 { left: 342px; }
  .flourish-3 { left: 613px; }

  .reason { position: absolute; top: 340px; width: 330px; text-align: center; color: var(--salmon); font-size: 37px; line-height: 32px; font-weight: 400; }
  .reason-kind { left: 22px; }
  .reason-worker { left: 291px; }
  .reason-essential { left: 562px; }

  .need { position: absolute; left: 856px; top: 94px; width: 300px; text-align: center; color: var(--teal); font-size: 38px; line-height: 32px; font-weight: 400; }
  .brand { position: absolute; left: 900px; top: 230px; width: 212px; display: flex; align-items: center; gap: 10px; color: var(--teal); font-size: 30px; line-height: 30px; }
  .brand-mark { width: 24px; height: 24px; background: var(--salmon); flex: none; }
  .reason-caregiver { position: absolute; left: 836px; top: 343px; width: 340px; text-align: center; color: var(--teal); font-size: 37px; line-height: 32px; font-weight: 400; }

  .perks { position: absolute; color: var(--white); font-size: 25px; line-height: 22px; }
  .perks-left { left: 68px; top: 478px; }
  .perks-left p:first-child { margin-bottom: 20px; }
  .perks-right { left: 576px; top: 478px; }
  .perks-right p:first-child { margin-bottom: 42px; }

  .extras { position: absolute; left: 965px; top: 482px; width: 165px; height: 101px; background: var(--white); color: var(--teal); font-size: 21px; text-align: center; padding-top: 1px; }
  .extras li { list-style: none; line-height: 33px; white-space: nowrap; }

  .contact { position: absolute; top: 620px; color: var(--teal); font-family: "Mulish", Arial, sans-serif; font-size: 21px; }
  .contact-web { left: 68px; }
  .contact-mail { left: 576px; }
</style>
</head>
<body>
<main class="ad">
  <div class="frame"></div>
  <div class="panel-top"></div>
  <div class="panel-contact"></div>

  <div class="photo photo-team" role="img" aria-label="Photo of three masked caregivers making heart shapes with their hands outdoors"></div>
  <div class="photo photo-nurse" role="img" aria-label="Photo of a smiling nurse with a stethoscope talking with a patient"></div>
  <div class="photo photo-board" role="img" aria-label="Photo of a chalkboard with the word essential in rainbow chalk and a pink heart"></div>

  <div class="flourish flourish-1" role="img" aria-label="Salmon wing-shaped ornament"></div>
  <div class="flourish flourish-2" role="img" aria-label="Salmon wing-shaped ornament"></div>
  <div class="flourish flourish-3" role="img" aria-label="Salmon wing-shaped ornament"></div>

  <h2 class="reason reason-kind">Because you<br>are Kind</h2>
  <h2 class="reason reason-worker">Because you<br>are a hard worker</h2>
  <h2 class="reason reason-essential">Because you<br>are essential</h2>

  <h1 class="need">We Need<br>You!</h1>
  <div class="brand"><span class="brand-mark"></span><span>Palmer Homecare</span></div>
  <h2 class="reason-caregiver">Because you<br>are a caregiver</h2>

  <div class="perks perks-left">
    <p>*Full-time &amp; Part-time Positions Available<br>(days, nights, weekdays, weekends)</p>
    <p>*Sign-on Bonus Programs Offered<br>Up to $500,00</p>
  </div>
  <div class="perks perks-right">
    <p>*Refer a Friend Bonus Program</p>
    <p>*2 Health Plans to Choose from<br>-Island-wide Locations</p>
  </div>

  <ul class="extras">
    <li>Holiday Pay</li>
    <li>401K Program</li>
    <li>Tuition Benefits</li>
  </ul>

  <p class="contact contact-web">To Find out more Visit www.........</p>
  <p class="contact contact-mail">email us help@......</p>
</main>
</body>
</html>
```